Easy Marinade Labels for Butchery Store

Need a set of labels designed for a Butchery Shop. They will sit in the top left corner of the packets as a triangle (7cm each side). Easy because the only major requirement is the label name and some small text saying "Please ask in store to see spec sheet for ingredients". Extra points for finding a fun way to incorporate the logo and/or images of food (garlic bulbs, chilli, spices ect) to enhance the label. List of Marinade Names below: GarlicPepper Mint & RosemarySatayBBQChilli Plum & GingerSundried Tomato & BasilBuffaloHoney SoyHoi-SinPer PeriSpicy CajunTeriyakiBlack Bean Ive also attached the logo and an example of how the label might sit on a packet of meat. Thanks

Target Market(s)

Butchery Deli Shop Customers

Industry/Entity Type

Food Store

Font styles to use
Serif
Sans Serif
Decorative
Other font styles liked:
• Fun font that isn't a generic Quellbrix Font?

Colors

Designer to choose colors to be used in the design.

Requirements
Must have
• Product Name
• Small text saying "Please ask in store to see spec sheet for ingredients"
Nice to have
• Photos of ingredients that would match that type of marinade - Chilli, Garlic, Spices.
• Fenly Oak Logo - not essential if it doesn't look good on the label / doesn't fit.

```html
<!DOCTYPE html>
<html lang="en">
<head>
<meta charset="utf-8">
<title>Fenly Oak – Buffalo Spices Marinade Label</title>
<link rel="stylesheet" href="https://fonts.googleapis.com/css2?family=Caveat+Brush&family=Montserrat:wght@700&family=Roboto+Condensed:wght@400&display=swap">
<style>
  :root {
    --paper: #ffffff;
    --frame-maroon: #6e1112;
    --flavour-red: #e2382a;
    --note-red: #b8403a;
    --logo-red: #a3161b;
  }
  html, body {
    margin: 0;
    padding: 0;
    width: 1200px;
    height: 900px;
    overflow: hidden;
    background: var(--paper);
  }
  .label {
    display: block;
    width: 1200px;
    height: 900px;
  }
  .label-frame { fill: var(--paper); stroke: var(--frame-maroon); stroke-width: 22; stroke-linejoin: miter; }
  .brand-name { font-family: "Montserrat", sans-serif; font-weight: 700; font-size: 22px; fill: var(--logo-red); letter-spacing: 1px; }
  .marinade-intro { font-family: "Montserrat", sans-serif; font-weight: 700; font-size: 16px; fill: var(--flavour-red); letter-spacing: 2.5px; }
  .marinade-name { font-family: "Caveat Brush", cursive; font-size: 86px; fill: var(--flavour-red); }
  .ingredient-note { font-family: "Roboto Condensed", sans-serif; font-size: 21px; fill: var(--note-red); letter-spacing: 2.4px; }
  .art-chilli-area { fill: url(#chilli-tones); }
  .art-tamarind-area { fill: url(#tamarind-tones); }
</style>
</head>
<body>
<svg class="label" viewBox="0 0 1200 900" xmlns="http://www.w3.org/2000/svg">
  <defs>
    <linearGradient id="chilli-tones" x1="0" y1="0" x2="0" y2="1">
      <stop offset="0" stop-color="#e8452f"/>
      <stop offset="0.6" stop-color="#c92a1e"/>
      <stop offset="1" stop-color="#6e3a30"/>
    </linearGradient>
    <linearGradient id="tamarind-tones" x1="0" y1="0" x2="0" y2="1">
      <stop offset="0" stop-color="#6a3a2a"/>
      <stop offset="0.55" stop-color="#a8744a"/>
      <stop offset="1" stop-color="#c9955e"/>
    </linearGradient>
    <clipPath id="label-inside">
      <polygon points="617,228 188,655 1045,655"/>
    </clipPath>
  </defs>

  <polygon class="label-frame" points="617,216 166,660 1068,660"/>

  <g clip-path="url(#label-inside)">
    <rect class="art-chilli-area" x="298" y="340" width="188" height="248" rx="24"
          role="img" aria-label="Photo of a red chilli pepper resting on dried spice pods"/>
    <rect class="art-tamarind-area" x="752" y="350" width="200" height="250" rx="24"
          role="img" aria-label="Photo of tamarind pods with scattered dark peppercorns"/>
  </g>

  <text class="brand-name" x="615" y="340" text-anchor="middle">Fenly Oak</text>

  <text class="marinade-intro" x="618" y="441" text-anchor="middle" textLength="174" lengthAdjust="spacingAndGlyphs">MARINATED WITH</text>
  <text class="marinade-name" x="618" y="519" text-anchor="middle" textLength="247" lengthAdjust="spacingAndGlyphs">BUFFALO</text>
  <text class="marinade-name" x="618" y="597" text-anchor="middle" textLength="205" lengthAdjust="spacingAndGlyphs">SPICES</text>

  <text class="ingredient-note" x="618" y="640" text-anchor="middle" textLength="606" lengthAdjust="spacingAndGlyphs">PLEASE ASK IN STORE TO SEE SPEC SHEET FOR INGREDIENTS</text>
</svg>
</body>
</html>
```